Adelaide based cleaning and remediation business needs a website design

We are launching a new company with no clients as yet so we don't have the benefit of Plimora Reviews to build confidence. We can use our  past work history with other employers in the industry to give some credibility. Happy to use any colour scheme as long as it look interesting when people click on the site it gets there attention. enquiry . I have supplied a mock up the important information and various photos as they tell a lot of the story.

```html
<!DOCTYPE html>
<html lang="en">
<head>
<meta charset="utf-8">
<title>Kalora Services Pty Ltd</title>
<link href="https://fonts.googleapis.com/css2?family=Poppins:wght@400;500;600;700;800&family=Lato:wght@400;700&display=swap" rel="stylesheet">
<style>
:root{
  --orange:#ff8a4c;
  --red:#f2442a;
  --yellow:#ffe556;
  --ink:#111;
  --text:#333;
  --cream:#fffbea;
  --dark:#000;
}
*{margin:0;padding:0;box-sizing:border-box}
html,body{width:1200px;height:3259px;overflow:hidden;background:#fff}
body{position:relative;font-family:'Lato',sans-serif;color:var(--text)}
.abs{position:absolute}
h1,h2,h3,.nav,.btn{font-family:'Poppins',sans-serif}

/* header */
.topbar{left:437px;top:0;width:763px;height:51px;border-bottom-left-radius:26px;background:linear-gradient(90deg,var(--red),var(--orange));color:#fff;font-family:'Poppins',sans-serif;font-size:16px;display:flex;align-items:center;padding-left:30px;gap:18px}
.topbar .sep{width:1px;height:18px;background:rgba(255,255,255,.6)}
.topbar svg{width:16px;height:16px;fill:#fff}
.logo{left:111px;top:6px;width:95px;height:126px;background:linear-gradient(#fff,#cfcfcf 60%,#888);border-radius:4px}
.nav{top:86px;font-size:15px;color:#111;font-weight:500}
.nav.active{color:var(--red)}
.btn{display:flex;align-items:center;justify-content:center;border-radius:30px;font-weight:700;font-size:15px}
.btn.yellow{background:var(--yellow);color:#111}

/* hero */
.hero{left:0;top:144px;width:1200px;height:545px;background:linear-gradient(90deg,#0b0b0b 0%,#1c1a18 45%,#3d3a36 60%,#4a6ea8 75%,#3d5f95 88%,#2a2a2a 100%)}
.hero-welcome{left:111px;top:230px;color:#fff;font-family:'Poppins',sans-serif;font-weight:600;font-size:20px}
.hero-title{left:111px;top:260px;color:#fff;font-size:52px;line-height:56px;font-weight:700}
.hero-text{left:111px;top:384px;color:#fff;font-size:15px;line-height:29px;width:440px}
.hero-btn{left:111px;top:455px;width:278px;height:50px;background:#fff;color:var(--red)}

.circle{border-radius:50%;color:#fff;text-align:center;display:flex;flex-direction:column;align-items:center;justify-content:center}
.circle.side{width:254px;height:254px;background:var(--orange);top:606px;color:#222}
.circle.side h3{font-size:20px;font-weight:700;line-height:28px;color:#111;margin-bottom:10px}
.circle.side p{font-size:14.5px;line-height:26px;padding:0 22px}
.circle.side a{font-family:'Poppins',sans-serif;font-size:17px;text-decoration:underline;color:#111;margin-top:8px}
.circle.mid{left:411px;top:568px;width:374px;height:374px;background:radial-gradient(circle at 50% 20%,#f7b23a,#f5722e 55%,#ee3b22);border:5px solid var(--yellow);border-left-color:#f4a43c}
.circle.mid h3{font-size:26px;line-height:32px;font-weight:600;margin-bottom:12px}
.circle.mid p{font-size:18px;line-height:32px;padding:0 38px}
.circle.mid a{font-family:'Poppins',sans-serif;font-size:18px;text-decoration:underline;color:#fff;margin-top:12px}

/* about */
.band{left:0;top:1315px;width:345px;height:90px;background:var(--yellow)}
.photo{border-radius:14px}
.about-h{left:644px;top:1080px;font-size:34px;font-weight:700;color:var(--ink)}
.about-p{left:644px;width:444px;font-size:15px;line-height:28.5px;text-align:justify}

/* testimonials */
.testi{left:0;top:1612px;width:1200px;height:611px;background:var(--cream)}
.sec-h{width:1200px;left:0;text-align:center;font-size:34px;font-weight:700;color:var(--ink)}
.avatar{border-radius:50%}
.quote{font-family:'Poppins',sans-serif;font-size:180px;line-height:1;color:#e3e1da;font-weight:800}
.dots{left:540px;top:2114px;display:flex;gap:8px}
.dots span{width:13px;height:13px;border-radius:50%;background:#cfd7ea}
.dots span.on{background:var(--orange)}

/* contact */
.form{left:675px;top:2362px;width:402px;height:472px;background:#fff;border-radius:22px;border-top:5px solid var(--yellow);box-shadow:0 6px 24px rgba(0,0,0,.12);padding:24px 27px;z-index:5}
.form h3{font-size:20px;font-weight:700;color:#111;margin-bottom:14px}
.field{border-bottom:1px solid #d8d8d8;height:58px;display:flex;align-items:flex-end;justify-content:space-between;padding-bottom:14px;font-size:14px;color:#555;margin-bottom:13px}
.field.msg{height:96px;align-items:flex-start;padding-top:32px}
.field i{width:12px;height:12px;border-radius:50%;background:#bbb;display:block}

/* footer */
.footer{left:0;top:2759px;width:1200px;height:500px;background:var(--dark);z-index:0}
.f-h{font-family:'Poppins',sans-serif;font-weight:700;font-size:17px;color:#fff}
.f-link{color:#fff;font-size:15px;display:flex;align-items:center;gap:10px}
.f-link svg{width:14px;height:14px}
.f-icon{width:32px;height:32px;border-radius:50%;background:#fff;display:flex;align-items:center;justify-content:center}
.f-icon svg{width:16px;height:16px;fill:#1d2a6e}
</style>
</head>
<body>

<header>
  <div class="abs topbar">
    <svg viewBox="0 0 24 24"><path d="M6.6 10.8a15 15 0 006.6 6.6l2.2-2.2a1 1 0 011-.25 11.4 11.4 0 003.6.6 1 1 0 011 1V20a1 1 0 01-1 1A17 17 0 013 4a1 1 0 011-1h3.5a1 1 0 011 1c0 1.25.2 2.45.6 3.6a1 1 0 01-.25 1z"/></svg>
    <span class="sep"></span><span>Call: 0400 555 018</span>
    <span style="width:20px"></span>
    <svg viewBox="0 0 24 24"><path d="M2 5h20v14H2z M2 5l10 8 10-8" stroke="#f5593a" stroke-width="1.5"/></svg>
    <span class="sep"></span><span>Mail: admin@kalorasvc.com</span>
    <span style="width:14px"></span>
    <span style="width:8px;height:8px;background:#fff;border-radius:2px"></span>
    <span style="width:8px;height:8px;background:#fff;border-radius:50%"></span>
  </div>
  <div class="abs logo" role="img" aria-label="Kalora Services logo illustration"></div>
  <a class="abs nav active" style="left:273px">HOME</a>
  <a class="abs nav" style="left:372px">ABOUT</a>
  <a class="abs nav" style="left:475px">SERVICES</a>
  <a class="abs nav" style="left:599px">TESTIMONIALS</a>
  <a class="abs nav" style="left:757px">NEWS</a>
  <a class="abs nav" style="left:853px">GALLERY</a>
  <a class="abs btn yellow" style="left:970px;top:75px;width:143px;height:41px">CONTACT US</a>
</header>

<section>
  <div class="abs hero" role="img" aria-label="Technician in blue protective suit and respirator inside a fire-damaged room"></div>
  <div class="abs hero-welcome">WELCOME TO</div>
  <h1 class="abs hero-title">KALORA SERVICES<br>PTY LTD</h1>
  <p class="abs hero-text">Adelaide-based Kalora Services is a family-run organisation.We havebeen in operation for more than two decades.</p>
  <a class="abs btn hero-btn">SCHEDULE A FREE INSPECTION</a>

  <div class="abs circle side" style="left:128px">
    <h3>Fire Damage<br>Clean Outs</h3>
    <p>Removal of debris;<br>On site cleaning of contents;<br>Cleaning of carpets and upholstered items</p>
    <a>Read More</a>
  </div>
  <div class="abs circle mid">
    <h3>PIGEON<br>WASTE CLEAN UPS</h3>
    <p>Can cause damage to buildings and spreaddisease, mites and bacteria, triggering alarmsand damaging the reputation of businesses.</p>
    <a>Read More</a>
  </div>
  <div class="abs circle side" style="left:807px">
    <h3>Squlaor Estate<br>Clean ups</h3>
    <p>Kalora Services is a hoarding clean up firm<br>that approaches clutter removal personally.</p>
    <a>Read More</a>
  </div>
</section>

<section>
  <div class="abs band"></div>
  <div class="abs photo" style="left:111px;top:1015px;width:223px;height:390px;background:linear-gradient(160deg,#c98a4a,#8a6a4a 40%,#2a2a2a)" role="img" aria-label="Worker in white coveralls cleaning beside a brick wall"></div>
  <div class="abs photo" style="left:345px;top:1111px;width:223px;height:391px;background:linear-gradient(170deg,#d9d4cc,#6d6a66 35%,#1e1e1e)" role="img" aria-label="Roof gutter covered with debris before cleaning"></div>
  <h2 class="abs about-h">ABOUT KALORA</h2>
  <p class="abs about-p" style="top:1133px">Adelaide-based Kalora Services is a family-run organisation.We have been in operation for more than two decades.We've gained some knowledge about cleaning and squalor removal services throughout the years.</p>
  <p class="abs about-p" style="top:1275px">As a small South Australian company, we base everything on responsibility honesty and fairness .We are aware of the confidence you put in us when you seek our help.</p>
  <a class="abs btn yellow" style="left:645px;top:1378px;width:153px;height:51px">READ MORE</a>
</section>

<section>
  <div class="abs testi"></div>
  <h2 class="abs sec-h" style="top:1670px">WHAT OUR CUSTOMER SAYS</h2>
  <div class="abs avatar" style="left:125px;top:1826px;width:66px;height:66px;background:#e8b79a" role="img" aria-label="Customer portrait"></div>
  <div class="abs avatar" style="left:1002px;top:1752px;width:46px;height:46px;background:#8a6a5a" role="img" aria-label="Customer portrait"></div>
  <div class="abs avatar" style="left:369px;top:1864px;width:14px;height:14px;background:var(--yellow)"></div>
  <div class="abs avatar" style="left:884px;top:1826px;width:7px;height:7px;background:var(--orange)"></div>
  <div class="abs avatar" style="left:531px;top:1751px;width:132px;height:132px;background:linear-gradient(#f3c9a8,#e9a47c)" role="img" aria-label="Portrait of Marina Delcourt"></div>
  <div class="abs quote" style="left:150px;top:1900px">“</div>
  <div class="abs quote" style="left:940px;top:2000px">”</div>
  <h3 class="abs" style="left:0;width:1200px;text-align:center;top:1906px;font-size:21px;font-weight:600;color:#222">MARINA DELCOURT</h3>
  <p class="abs" style="left:0;width:1200px;text-align:center;top:1942px;font-size:12px;font-family:'Poppins',sans-serif;color:#666">United States</p>
  <p class="abs" style="left:0;width:1200px;text-align:center;top:1958px;font-size:32px;color:#f5b52e;letter-spacing:-2px">★★★★★</p>
  <p class="abs" style="left:265px;width:670px;text-align:center;top:2004px;font-size:16px;line-height:30px;color:#444">Tomas and his team arrived the next morning to clean up a rental property my husband and I own which and had been trashed by the tenants.He was the only contractor to return my call. They did an amazing job and alsodeodorised the house for no extra charge.</p>
  <div class="abs dots"><span></span><span></span><span></span><span class="on"></span><span></span><span></span></div>
</section>

<footer>
  <div class="abs footer"></div>
  <div class="abs" style="left:111px;top:2923px;width:278px;height:197px;background:#e6e9ee" role="img" aria-label="Street map showing the office location"></div>
  <h4 class="abs f-h" style="left:441px;top:2918px">QUICK LINKS</h4>
  <a class="abs f-link" style="left:441px;top:2962px"><svg viewBox="0 0 24 24" fill="#fff"><path d="M4 11h12l-5-5 1.5-1.5L20 12l-7.5 7.5L11 18l5-5H4z"/></svg>Home</a>
  <a class="abs f-link" style="left:441px;top:2996px"><svg viewBox="0 0 24 24" fill="#fff"><path d="M4 11h12l-5-5 1.5-1.5L20 12l-7.5 7.5L11 18l5-5H4z"/></svg>About</a>
  <a class="abs f-link" style="left:441px;top:3030px"><svg viewBox="0 0 24 24" fill="#fff"><path d="M4 11h12l-5-5 1.5-1.5L20 12l-7.5 7.5L11 18l5-5H4z"/></svg>Services</a>
  <a class="abs f-link" style="left:441px;top:3064px"><svg viewBox="0 0 24 24" fill="#fff"><path d="M4 11h12l-5-5 1.5-1.5L20 12l-7.5 7.5L11 18l5-5H4z"/></svg>Testimonials</a>
  <a class="abs f-link" style="left:441px;top:3098px"><svg viewBox="0 0 24 24" fill="#fff"><path d="M4 11h12l-5-5 1.5-1.5L20 12l-7.5 7.5L11 18l5-5H4z"/></svg>Contact Us</a>

  <h4 class="abs f-h" style="left:617px;top:2918px">CONTACT US</h4>
  <div class="abs f-icon" style="left:617px;top:2965px"><svg viewBox="0 0 24 24"><path d="M12 2a7 7 0 00-7 7c0 5 7 13 7 13s7-8 7-13a7 7 0 00-7-7zm0 9.5A2.5 2.5 0 1112 6.5a2.5 2.5 0 010 5z"/></svg></div>
  <p class="abs" style="left:661px;top:2961px;color:#fff;font-size:15px;line-height:27px">14 Wattle Lane<br>Parkside SA 5063</p>
  <div class="abs f-icon" style="left:617px;top:3027px"><svg viewBox="0 0 24 24"><path d="M6.6 10.8a15 15 0 006.6 6.6l2.2-2.2a1 1 0 011-.25 11.4 11.4 0 003.6.6 1 1 0 011 1V20a1 1 0 01-1 1A17 17 0 013 4a1 1 0 011-1h3.5a1 1 0 011 1c0 1.25.2 2.45.6 3.6a1 1 0 01-.25 1z"/></svg></div>
  <p class="abs" style="left:661px;top:3033px;color:#fff;font-size:15px">0400 555 018</p>
  <div class="abs f-icon" style="left:617px;top:3078px"><svg viewBox="0 0 24 24"><path d="M3 6h18v12H3z"/><path d="M3 6l9 7 9-7" stroke="#fff" stroke-width="1.6" fill="none"/></svg></div>
  <p class="abs" style="left:661px;top:3084px;color:#fff;font-size:15px">admin@kalorasvc.com</p>

  <div class="abs" style="left:913px;top:2922px;width:143px;height:182px;background:linear-gradient(#fff,#d0d0d0 60%,#9a9a9a)" role="img" aria-label="Kalora Services logo illustration"></div>
  <div class="abs" style="left:110px;top:3170px;width:977px;height:1px;background:#777"></div>
  <p class="abs" style="left:0;width:1200px;text-align:center;top:3205px;color:#fff;font-size:15px">Copyrights@2025.Kalora.All Rights Reserved</p>
</footer>

<section>
  <h2 class="abs sec-h" style="top:2283px">GET IN TOUCH WITH US</h2>
  <h3 class="abs" style="left:113px;top:2355px;font-size:25px;font-weight:700;color:#111">CONTACT US</h3>
  <p class="abs" style="left:115px;top:2403px;width:430px;font-size:15px;line-height:29px;color:#333">As a small South Australian company, we base everything on responsibilityhonesty and fairness .</p>
  <div class="abs" style="left:114px;top:2489px;width:38px;height:38px;border-radius:50%;background:var(--orange);display:flex;align-items:center;justify-content:center">
    <svg viewBox="0 0 24 24" width="20" height="20" fill="#fff"><path d="M6.6 10.8a15 15 0 006.6 6.6l2.2-2.2a1 1 0 011-.25 11.4 11.4 0 003.6.6 1 1 0 011 1V20a1 1 0 01-1 1A17 17 0 013 4a1 1 0 011-1h3.5a1 1 0 011 1c0 1.25.2 2.45.6 3.6a1 1 0 01-.25 1z"/></svg>
  </div>
  <p class="abs" style="left:168px;top:2488px;font-size:10px;font-family:'Poppins',sans-serif;color:var(--orange)">CALL NOW</p>
  <p class="abs" style="left:168px;top:2505px;font-size:22px;font-family:'Poppins',sans-serif;font-weight:600;color:var(--orange)">0400 555 018</p>
  <div class="abs" style="left:118px;top:2578px;width:90px;height:90px;border-radius:50%;background:#d4a23a;border:8px solid #1a1a1a" role="img" aria-label="Quality guarantee badge"></div>
  <div class="abs" style="left:248px;top:2588px;width:88px;height:88px;border-radius:50%;background:linear-gradient(135deg,#4fbf4a,#1d9fd0)" role="img" aria-label="Cleaning certification badge"></div>
  <div class="abs" style="left:346px;top:2602px;width:134px;height:56px;border-radius:6px;background:#e6e8ee" role="img" aria-label="Certification body badge"></div>

  <form class="abs form">
    <h3>SEND US A MESSAGE</h3>
    <div class="field">Name<i></i></div>
    <div class="field">Email<i></i></div>
    <div class="field">Phone Number<i></i></div>
    <div class="field msg">Message<i></i></div>
    <a class="btn yellow" style="width:120px;height:44px;margin-top:18px">SUBMIT</a>
  </form>
</section>

</body>
</html>
```